I need a SEO-friendly Wordpress website (making sure to style H1, H2, H3, etc correctly) for a Hawaii-based law firm called Meridian Crest Legal Group. Comparable websites include https://brvlaw.example/ and https://www.lomrit.example/ for design reference. The current copy on the TarnAdvocate.example website can be used.

```html
<!DOCTYPE html>
<html lang="en">
<head>
<meta charset="utf-8">
<title>Meridian Crest Legal Group</title>
<link rel="stylesheet" href="https://fonts.googleapis.com/css2?family=Lexend:wght@400;500&family=Lato:ital,wght@0,400;0,700;1,400&display=swap">
<style>
:root{
  --accent:#b0600f;
  --accent-dark:#8a4a0b;
  --ink:#1e1e1e;
  --muted:#5e5e5e;
  --band:#2c2a28;
  --rule:#7a2c0c;
  --field:#d7d7d7;
  --white:#ffffff;
}
*{box-sizing:border-box;margin:0;padding:0}
html,body{width:1200px;height:3499px;overflow:hidden;background:var(--white)}
body{position:relative;font-family:'Lato',sans-serif;color:var(--ink)}
.abs{position:absolute}
h1,h2,h3,h4{font-family:'Lexend',sans-serif;font-weight:500}
.btn{position:absolute;display:flex;align-items:center;justify-content:center;border-radius:20px;background:var(--accent);color:var(--white);font-family:'Lexend',sans-serif;font-size:13px;text-decoration:none}
.eyebrow{position:absolute;display:flex;align-items:center;gap:14px;color:var(--accent);font-family:'Lexend',sans-serif;font-size:15px;letter-spacing:.3px}
.eyebrow::before{content:"";display:block;width:51px;height:1px;background:var(--accent)}
.section-title{position:absolute;left:163px;font-size:30px;color:var(--ink);line-height:1}

/* header + hero */
.hero{position:absolute;left:0;top:0;width:1200px;height:599px}
.hero-media{position:absolute;inset:0;background:linear-gradient(90deg,#3a3632 0%,#24201c 35%,#1b1612 60%,#2a1f16 100%)}
.hero-shade{position:absolute;inset:0;background:linear-gradient(180deg,rgba(0,0,0,.15),rgba(0,0,0,.45))}
.site-header{position:absolute;left:0;top:0;width:1200px;height:60px;background:rgba(150,84,12,.88)}
.brand{position:absolute;left:163px;top:16px;font-family:'Lexend',sans-serif;font-weight:500;font-size:22px;color:var(--white)}
.nav{position:absolute;top:22px;left:0;width:1200px;list-style:none}
.nav li{position:absolute;font-size:12px;color:var(--white)}
.hero h1{position:absolute;left:0;top:205px;width:1200px;text-align:center;color:var(--white);font-size:49px;line-height:50px}
.hero-sub{position:absolute;left:0;top:325px;width:1200px;text-align:center;color:var(--white);font-size:12px}
.btn-hero{font-size:18px;border-radius:24px}
.btn-outline{background:transparent;border:1px solid var(--accent);color:var(--accent)}

/* about */
.about-text{position:absolute;left:163px;width:406px;font-size:11.5px;line-height:19.6px;color:var(--muted)}
.photo{position:absolute}

/* practice cards */
.card{position:absolute;top:1261px;width:277px;height:187px;overflow:hidden}
.card-title{position:absolute;left:13px;font-family:'Lexend',sans-serif;font-size:16px;color:var(--white)}
.card-rule{position:absolute;left:13px;height:2px;background:var(--accent)}
.chev{position:absolute;width:24px;height:24px}
.card-body{position:absolute;left:13px;top:62px;width:250px;font-size:11px;line-height:19.5px;color:var(--white)}

/* band */
.band{position:absolute;left:0;top:1618px;width:1200px;height:270px;background:linear-gradient(90deg,#2a2a2a 0%,#33291f 40%,#2e2822 70%,#2a2a2a 100%)}
.vline{position:absolute;left:600px;width:1px;background:var(--accent)}
.band h2{position:absolute;left:0;top:85px;width:1200px;text-align:center;color:var(--accent);font-size:30px}
.band p{position:absolute;left:290px;top:143px;width:620px;text-align:center;color:#e8e8e8;font-style:italic;font-size:13.5px;line-height:21px}

/* team */
.arrow{position:absolute;top:2000px;width:26px;height:26px}
.attorney-name{position:absolute;left:406px;top:2110px;font-size:23px}
.attorney-bio{position:absolute;left:406px;top:2150px;width:560px;font-style:italic;font-size:13.5px;line-height:21px;color:var(--muted)}

/* contact */
.field{position:absolute;border:1px solid var(--field);border-radius:4px;background:var(--white);font-size:11.5px;color:#666;padding:15px 0 0 16px}
.query h2{position:absolute;left:0;top:2844px;width:1200px;text-align:center;color:var(--accent);font-size:30px}
.query p{position:absolute;left:280px;top:2903px;width:640px;text-align:center;font-style:italic;font-size:13.5px;line-height:21px;color:var(--muted)}

/* footer */
.footer{position:absolute;left:0;top:3100px;width:1200px;height:399px;border-top:3px solid var(--rule)}
.footer-deco{position:absolute;left:420px;top:25px;width:380px;height:300px;background:radial-gradient(ellipse at center,rgba(150,100,60,.14),rgba(255,255,255,0) 70%)}
.footer h3{position:absolute;top:60px;font-size:16.5px;text-decoration:underline;text-underline-offset:4px;color:var(--ink)}
.flist{position:absolute;top:127px;list-style:none;font-size:11.5px;line-height:22.6px;color:var(--muted)}
.info-icon{position:absolute;left:161px;width:36px;height:36px}
.info-text{position:absolute;left:209px;font-size:11.5px;line-height:19.5px;color:var(--muted)}
.social{position:absolute;top:244px;width:34px;height:34px;border:1.5px solid var(--accent);border-radius:50%}
.subscribe-field{position:absolute;left:836px;top:119px;width:202px;height:45px;background:#eeeeee;border:1px solid #dcdcdc;font-size:11px;color:#777;padding:16px 0 0 12px}
.map-link{position:absolute;left:837px;top:231px;font-size:11.5px;color:var(--ink);text-decoration:underline}
.footer-rule{position:absolute;left:163px;top:335px;width:875px;height:1px;background:#dddddd}
.copyright{position:absolute;left:0;top:358px;width:1200px;text-align:center;font-size:11.5px;color:#444}
</style>
</head>
<body>

<header class="hero">
  <div class="hero-media" role="img" aria-label="Library shelves of old law books with a row of marble busts"></div>
  <div class="hero-shade"></div>
  <div class="site-header">
    <div class="brand">Meridian Crest Legal Group</div>
    <ul class="nav">
      <li style="left:644px">Home</li>
      <li style="left:707px">Practice Area</li>
      <li style="left:821px">Attroneys</li>
      <li style="left:915px">Blog</li>
      <li style="left:973px">Contact Us</li>
    </ul>
  </div>
  <h1>Deeper Understanding Better<br>Solutions</h1>
  <p class="hero-sub">Dedicated to making sure you receive the care and attention you need</p>
  <a class="btn btn-hero" style="left:470px;top:381px;width:134px;height:47px">Contact Us</a>
  <a class="btn btn-hero btn-outline" style="left:617px;top:381px;width:119px;height:47px">Join Now</a>
</header>

<section class="about">
  <div class="eyebrow" style="left:163px;top:674px">ABOUT US</div>
  <h2 class="section-title" style="top:705px">The Kona Lawyers of MCLG</h2>
  <p class="about-text" style="top:781px">The experienced attorneys in the Meridian Crest Legal Group's Kailua Kona, Hawaii office provide clients with a wide range of litigation expertise, including legal claims involving divorce &amp; family, personal injury, toxic exposures, intellectual property, and real estate.</p>
  <p class="about-text" style="top:879px">Our Kona office also offers commercial and hospitality litigation expertise on behalf of a wide variety of clients, including restaurants, hotels, property owners, and many others. We never wish to see our clients go to court, though if there is no other option, you're in safe hands with our seasoned trial lawyers and the many years of courtroom experience behind them.</p>
  <a class="btn" style="left:161px;top:1015px;width:90px;height:38px">Learn More</a>
  <div class="photo" style="left:611px;top:704px;width:213px;height:184px;background:linear-gradient(180deg,#8d9aa6,#4a5560 60%,#2a2f36)" role="img" aria-label="Group of firm attorneys in suits standing outdoors"></div>
  <div class="photo" style="left:841px;top:660px;width:195px;height:228px;background:linear-gradient(160deg,#c9a77a,#6a5545 50%,#2f3440)" role="img" aria-label="Attorneys smiling in a meeting"></div>
  <div class="photo" style="left:734px;top:903px;width:304px;height:150px;background:linear-gradient(90deg,#5b3418,#8c5a2e 50%,#d9c3a0)" role="img" aria-label="Wooden gavel resting on stacked law books"></div>
</section>

<section class="practice">
  <div class="eyebrow" style="left:163px;top:1142px">WHAT WE DO</div>
  <h2 class="section-title" style="top:1171px">The Kona Lawyers of MCLG</h2>

  <article class="card" style="left:161px;background:linear-gradient(180deg,#6b5a48,#3a2f26)" role="img" aria-label="Couple in discussion at home">
    <h3 class="card-title" style="top:124px">Family &amp; Divorce</h3>
    <svg class="chev" style="left:228px;top:121px" viewBox="0 0 24 24"><circle cx="12" cy="12" r="11" fill="none" stroke="#fff" stroke-width="1.2"/><path d="M10 7l5 5-5 5" fill="none" stroke="#fff" stroke-width="1.4"/></svg>
    <div class="card-rule" style="top:157px;width:250px"></div>
  </article>

  <article class="card" style="left:461px;background:var(--accent)">
    <h3 class="card-title" style="top:17px">Personal Injury</h3>
    <svg class="chev" style="left:228px;top:16px" viewBox="0 0 24 24"><circle cx="12" cy="12" r="12" fill="#fff"/><path d="M10 7l5 5-5 5" fill="none" stroke="#8a4a0b" stroke-width="1.4"/></svg>
    <div class="card-rule" style="top:52px;width:210px;background:#fff"></div>
    <p class="card-body">Dealing with personal injury and wrongful death claims is hard enough, so the lawyers of MCLG are here to make things as easy on you as possible. From Kailua Kona to Hilo, Hawaii to California, our attorneys are here for you.</p>
  </article>

  <article class="card" style="left:761px;background:linear-gradient(180deg,#6e7580,#2f3238)" role="img" aria-label="Team of corporate professionals">
    <h3 class="card-title" style="top:124px">Corporate &amp; IP</h3>
    <svg class="chev" style="left:228px;top:121px" viewBox="0 0 24 24"><circle cx="12" cy="12" r="11" fill="none" stroke="#fff" stroke-width="1.2"/><path d="M10 7l5 5-5 5" fill="none" stroke="#fff" stroke-width="1.4"/></svg>
    <div class="card-rule" style="top:157px;width:210px"></div>
  </article>

  <a class="btn" style="left:555px;top:1508px;width:90px;height:38px">View All</a>
</section>

<section class="band" role="img" aria-label="Dark background of a gavel on a desk">
  <div class="vline" style="top:0;height:60px"></div>
  <h2>Nationwide Law Firm Presence</h2>
  <p>Kailua Kona serves as the firm's West Coast headquarters for litigation and representation on behalf of individuals and corporations involved in a wide range of legal matters. The firm and its attorneys are licensed to practice and represent clients in Hawaii, California, Arizona, Texas, and Washington D.C.</p>
</section>

<section class="team">
  <div class="eyebrow" style="left:163px;top:1964px">OUR TEAM</div>
  <h2 class="section-title" style="top:1994px">View Our Attorneys</h2>
  <svg class="arrow" style="left:973px" viewBox="0 0 26 26"><circle cx="13" cy="13" r="13" fill="var(--accent)"/><path d="M15 8l-5 5 5 5" fill="none" stroke="#fff" stroke-width="1.6"/></svg>
  <svg class="arrow" style="left:1011px" viewBox="0 0 26 26"><circle cx="13" cy="13" r="13" fill="var(--accent)"/><path d="M11 8l5 5-5 5" fill="none" stroke="#fff" stroke-width="1.6"/></svg>
  <div class="photo" style="left:161px;top:2087px;width:209px;height:211px;background:linear-gradient(180deg,#3a3f6a,#7c6a62 55%,#2a3048)" role="img" aria-label="Portrait of attorney Dorian Halvey"></div>
  <h3 class="attorney-name">Dorian Halvey ESQ.</h3>
  <p class="attorney-bio">The experienced attorneys in the Meridian Crest Legal Group's Kailua Kona, Hawaii office provide clients with a wide range of litigation expertise, including legal claims involving divorce &amp; family, personal injury, toxic exposures, intellectual property, and real estate.</p>
  <a class="btn" style="left:406px;top:2253px;width:88px;height:35px">Read More</a>
</section>

<section class="contact">
  <div class="eyebrow" style="left:163px;top:2382px">CONTACT INFO</div>
  <h2 class="section-title" style="top:2412px">Get In Touch</h2>
  <div class="field" style="left:161px;top:2488px;width:281px;height:45px">Name:</div>
  <div class="field" style="left:459px;top:2488px;width:281px;height:45px">Email:</div>
  <div class="field" style="left:756px;top:2488px;width:282px;height:45px">Phone:</div>
  <div class="field" style="left:161px;top:2547px;width:877px;height:90px;border-radius:8px">Message:</div>
  <a class="btn" style="left:548px;top:2675px;width:102px;height:37px">Submit Now</a>
</section>

<section class="query">
  <div class="vline" style="top:2760px;height:63px"></div>
  <h2>If You Have An Any Query</h2>
  <p>Lorem Ipsum is simply dummy text of the printing and typesetting industry. Lorem Ipsum has been the industry's standard dummy text ever since the 1500s.</p>
  <a class="btn" style="left:555px;top:2992px;width:90px;height:37px">Let's Talk</a>
</section>

<footer class="footer">
  <div class="footer-deco" role="img" aria-label="Faint gavel and law lettering decoration"></div>

  <h3 style="left:163px">Our Info</h3>
  <svg class="info-icon" style="top:115px" viewBox="0 0 36 36"><circle cx="18" cy="18" r="17" fill="none" stroke="var(--accent)" stroke-width="1.3"/><path d="M12 10c1-1 2-1 3 0l2 3c.5 1 0 2-1 2.5 1 2 2.5 3.5 4.5 4.5.5-1 1.5-1.5 2.5-1l3 2c1 1 1 2 0 3-2 2-5 1.5-9-2.5s-4.5-7-5-11.5z" fill="var(--accent)"/></svg>
  <div class="info-text" style="top:124px">+1.808.555.0142</div>
  <svg class="info-icon" style="top:173px" viewBox="0 0 36 36"><circle cx="18" cy="18" r="17" fill="none" stroke="var(--accent)" stroke-width="1.3"/><rect x="10" y="12" width="16" height="12" fill="none" stroke="var(--accent)" stroke-width="1.6"/><path d="M10 12l8 7 8-7" fill="none" stroke="var(--accent)" stroke-width="1.6"/></svg>
  <div class="info-text" style="top:182px">clients@tarnadvocate.example</div>
  <svg class="info-icon" style="top:231px" viewBox="0 0 36 36"><circle cx="18" cy="18" r="17" fill="none" stroke="var(--accent)" stroke-width="1.3"/><path d="M18 27s-6-7-6-11a6 6 0 0112 0c0 4-6 11-6 11z" fill="var(--accent)"/><circle cx="18" cy="16" r="2.2" fill="#fff"/></svg>
  <div class="info-text" style="top:233px">48-210 Lanakila Road,<br>Suite 305, Kailua Kona,<br>Hawaii 96740.</div>

  <h3 style="left:388px">Practice Areas</h3>
  <ul class="flist" style="left:388px"><li>Family Law</li><li>Personal Injury</li><li>Corporate &amp; Id</li><li>Real Estate</li></ul>
  <div class="social" style="left:387px"></div>
  <div class="social" style="left:432px"></div>
  <div class="social" style="left:477px"></div>
  <div class="social" style="left:523px"></div>

  <h3 style="left:612px">Quick Link</h3>
  <ul class="flist" style="left:613px"><li>Home</li><li>About us</li><li>Practice Areas</li><li>Attroneys</li><li>Blog</li><li>Contant Us</li></ul>

  <h3 style="left:837px">News Letter</h3>
  <div class="subscribe-field">Email:</div>
  <a class="btn" style="left:836px;top:173px;width:90px;height:38px">Subscribe!</a>
  <a class="map-link">Get Direction of Map</a>

  <div class="footer-rule"></div>
  <p class="copyright">Copyrights 2019 © Meridian Crest Legal Group. All Rights Reserved. Terms &amp; Conditions | Privacy Policy</p>
</footer>

</body>
</html>
```